Modern Medical Optometry Website

We need mordern, Patient friendly website. Easy to navigate and enhance our advance medical technology and excellent patient care.
1. HOME PAGE
2. OUR TEAM PAGE
3. EYECARE PAGE - VISION SERVICES, EYE EXAMS, KERATOCONUS CENTER, GLAUCOMA , DIABITES, MELORIDEX EXAM, DIGITAL RETINAL, OCT.
4. MYOPIA CONTROL CLINIC
5. DRY EYE CLINIC
6. EYEWEAR
7. PATIENT CENTER - BLOG
7. CONTACT US
This is our current website www.brivaloka.com
and We want to add more content and a cleaner design like these website
http://tarnwickfolvendale.com/
https://www.qmvorlu.com/

```html
<!DOCTYPE html>
<html lang="en">
<head>
<meta charset="utf-8">
<title>Lumora Optometry</title>
<link rel="stylesheet" href="https://fonts.googleapis.com/css2?family=Lato:wght@300;400;700;900&display=swap">
<style>
:root{
  --teal:#167a97;
  --teal-dark:#0f6783;
  --yellow:#f6c623;
  --ink:#2b2b2b;
  --muted:#666;
  --cream:#fdfbea;
  --footer:#1d1d1d;
  --white:#fff;
}
*{box-sizing:border-box;margin:0;padding:0}
html,body{width:1200px;height:4986px;overflow:hidden}
body{font-family:'Lato',sans-serif;color:var(--ink);background:var(--white);position:relative}
section,header,footer{position:relative;width:1200px;overflow:hidden}
.abs{position:absolute}
.title{font-weight:400;font-size:36px;color:var(--teal);text-align:center;letter-spacing:1px}
.pill{display:inline-block;background:var(--yellow);color:var(--white);font-weight:700;border-radius:30px;text-align:center}
.arrow{position:absolute;width:48px;height:48px;border-radius:50%;border:2px solid #999;background:var(--white);display:flex;align-items:center;justify-content:center}
.arrow svg{width:18px;height:18px}

/* header */
.site-header{height:126px;background:var(--white);overflow:visible;z-index:5}
.brand-disc{position:absolute;left:125px;top:-60px;width:200px;height:245px;border-radius:0 0 100px 100px;background:var(--white);display:flex;flex-direction:column;align-items:center;justify-content:flex-end;padding-bottom:28px;gap:8px}
.brand-mark{width:44px;height:44px;background:var(--yellow)}
.brand-name{font-size:17px;font-weight:700;color:var(--teal);letter-spacing:1px}
.top-contact{position:absolute;left:575px;top:26px;font-size:18px;color:var(--teal);display:flex;align-items:center;gap:10px}
.top-contact b{font-weight:700}
.top-btn{position:absolute;left:892px;top:22px;width:197px;height:42px;line-height:42px;font-size:16px}
.nav{position:absolute;left:350px;top:82px;display:flex;align-items:center;gap:22px;font-size:13px;font-weight:700;color:#333}
.nav .home{width:30px;height:30px;border-radius:50%;background:var(--teal);display:flex;align-items:center;justify-content:center}

/* hero */
.hero{height:625px}
.hero-photo{position:absolute;inset:0;background:radial-gradient(circle at 50% 45%,#2c5fa0 0,#3b78b8 60px,#9aa6b3 140px,#c9ccd0 260px,#9a9ea3 520px,#6f7378 800px)}
.hero h1{position:absolute;top:255px;width:100%;text-align:center;color:var(--white);font-weight:400;font-size:68px;letter-spacing:2px}
.hero p{position:absolute;top:350px;width:100%;text-align:center;color:var(--white);font-size:20px}
.hero .pill{position:absolute;left:470px;top:430px;width:265px;height:60px;line-height:60px;font-size:19px}
.hero .arrow{top:348px;border-color:var(--white);background:rgba(0,0,0,.25)}
.notch{position:absolute;left:575px;bottom:-25px;width:50px;height:50px;border-radius:50%;background:var(--white)}

/* promise */
.promise{height:449px}
.promise .title{position:absolute;top:140px;width:100%}
.promise-text{position:absolute;top:225px;left:200px;width:800px;text-align:center;font-size:13px;line-height:26px;color:var(--muted)}
.promise-text p{margin-bottom:10px}

/* services */
.services{height:688px;background:linear-gradient(var(--white) 0 73px,var(--teal) 73px)}
.ghost{position:absolute;width:100%;text-align:center;font-size:110px;font-weight:900;color:rgba(255,255,255,.07);letter-spacing:4px}
.service-card{position:absolute;width:300px;height:215px;overflow:hidden}
.service-card .photo{position:absolute;inset:0 0 30px 0}
.service-card .cap{position:absolute;left:0;right:0;bottom:0;height:30px;background:var(--yellow);color:#333;font-size:12px;font-weight:900;text-align:center;line-height:30px}
.more-btn{position:absolute;left:474px;top:542px;width:252px;height:50px;line-height:48px;border:2px solid var(--white);border-radius:30px;color:var(--white);font-size:14px;font-weight:700;text-align:center}

/* team */
.team{height:592px}
.team .title{position:absolute;top:135px;width:100%}
.team-card{position:absolute;top:253px;width:300px;height:266px;border-radius:20px;overflow:hidden}
.team-card.feature{background:var(--white);box-shadow:0 4px 18px rgba(0,0,0,.18)}
.team-card.feature .photo{position:absolute;left:80px;top:16px;width:140px;height:170px;border:4px solid #d9c38a}
.team-card.feature .label{position:absolute;left:0;right:0;bottom:0;height:66px;background:var(--yellow);padding:16px 0 0 26px;color:var(--white)}
.label .nm{font-size:15px;font-weight:900}
.label .rl{font-size:12px}
.label .go{position:absolute;right:22px;top:17px;width:34px;height:34px;border-radius:50%;background:var(--white);display:flex;align-items:center;justify-content:center}

/* dry eye */
.dry{height:645px}
.dry-photo{position:absolute;left:0;top:66px;width:600px;height:446px;background:linear-gradient(120deg,#c79a76,#e6c3a5 45%,#3b2b24 80%)}
.dry-frame{position:absolute;left:540px;top:66px;width:60px;height:446px;background:var(--white)}
.play{position:absolute;left:250px;top:240px;width:100px;height:100px;border-radius:50%;border:5px solid var(--white);display:flex;align-items:center;justify-content:center}
.dry h2{position:absolute;left:640px;top:132px;font-size:36px;font-weight:400;color:var(--teal)}
.dry p{position:absolute;left:640px;top:200px;width:440px;font-size:13px;line-height:28px;color:var(--muted)}
.dry .pill{position:absolute;left:640px;top:385px;width:140px;height:40px;line-height:40px;font-size:14px}

/* reviews */
.reviews{height:548px;background:var(--cream)}
.reviews .title{position:absolute;top:105px;width:100%}
.review{position:absolute;top:252px;width:300px;height:180px;background:var(--white);border:1px solid #ddd;text-align:center;padding:42px 28px 0}
.review .q{position:absolute;left:134px;top:-18px;width:34px;height:34px;border-radius:50%;background:var(--yellow);color:var(--white);font-size:20px;font-weight:900;line-height:38px}
.review p{font-size:14px;font-style:italic;line-height:22px;color:#444}
.review .src{margin-top:12px;font-size:15px;font-weight:700;color:#444;display:flex;justify-content:center;align-items:center;gap:6px}
.review .src i{display:inline-block;width:12px;height:12px;background:#888}

/* partners */
.partners{height:207px;display:flex;align-items:center;justify-content:center;gap:62px}
.partner{width:86px;height:44px;border-radius:6px;background:#3a3a3a}
.partner.round{width:48px;border-radius:50%}

/* contact */
.contact{height:840px}
.contact .title{position:absolute;top:65px;width:100%;color:var(--teal)}
.band{position:absolute;left:0;top:105px;width:1200px;height:310px}
.contact-item{position:absolute;top:152px;width:220px;color:var(--white);font-size:14px;line-height:22px}
.contact-item .ic{width:46px;height:46px;border-radius:50%;background:var(--yellow);display:flex;align-items:center;justify-content:center;margin-bottom:18px}
.map{position:absolute;left:0;top:325px;width:1200px;height:515px;background:linear-gradient(135deg,#dfe3d8,#eceee8 50%,#d6e2ec)}
.info{position:absolute;top:484px;height:223px;background:var(--yellow);color:var(--white);padding:22px 36px}
.info h3{font-size:22px;font-weight:700;margin-bottom:14px}
.info li{list-style:none;font-size:12px;line-height:20px}

/* footer */
.site-footer{height:266px;background:var(--footer);color:var(--white)}
.social{position:absolute;top:66px;left:0;right:0;display:flex;justify-content:center;gap:20px}
.social span{width:40px;height:40px;border-radius:50%;border:1px solid #777}
.foot-nav{position:absolute;top:150px;width:100%;text-align:center;font-size:12px;font-weight:700;letter-spacing:.5px}
.foot-nav span{margin:0 10px;color:#aaa}
.copy{position:absolute;top:198px;width:100%;text-align:center;font-size:12px;color:#bbb}
</style>
</head>
<body>

<header class="site-header">
  <div class="brand-disc">
    <div class="brand-mark"></div>
    <div class="brand-name">LUMORA</div>
  </div>
  <div class="top-contact">
    <svg width="18" height="18" viewBox="0 0 24 24"><path fill="#167a97" d="M6.6 10.8a15 15 0 0 0 6.6 6.6l2.2-2.2c.3-.3.7-.4 1-.2 1.1.4 2.3.6 3.6.6.6 0 1 .4 1 1V20c0 .6-.4 1-1 1A17 17 0 0 1 3 4c0-.6.4-1 1-1h3.5c.6 0 1 .4 1 1 0 1.3.2 2.5.6 3.6.1.3 0 .7-.2 1z"/></svg>
    <span><b>555-014-2010</b> / Call Or Text Us</span>
  </div>
  <div class="pill top-btn">Make An Appointment</div>
  <nav class="nav">
    <span class="home"><svg width="14" height="14" viewBox="0 0 24 24"><path fill="#fff" d="M12 3 2 12h3v8h5v-6h4v6h5v-8h3z"/></svg></span>
    <span>OUR TEAM</span><span>EYECARE</span><span>MYOPIA CONTROL CLINIC</span><span>DRY EYE CLINIC</span><span>EYEWEAR</span><span>PATIENT CENTER</span><span>CONTACT US</span>
  </nav>
</header>

<section class="hero">
  <div class="hero-photo" role="img" aria-label="Close-up photograph of a blue eye"></div>
  <h1>LUMORA OPTOMETRY</h1>
  <p>Sed ut perspiciatis unde omnis iste natus error sit voluptatem</p>
  <div class="pill">Make An Appointment</div>
  <div class="arrow" style="left:75px"><svg viewBox="0 0 24 24"><path d="M15 4 7 12l8 8" fill="none" stroke="#fff" stroke-width="3"/></svg></div>
  <div class="arrow" style="left:1078px"><svg viewBox="0 0 24 24"><path d="m9 4 8 8-8 8" fill="none" stroke="#fff" stroke-width="3"/></svg></div>
  <div class="notch"></div>
</section>

<section class="promise">
  <h2 class="title">THE LUMORA PROMISE</h2>
  <div class="promise-text">
    <p>Welcome to Lumora Optometry, where your vision and eye health are our sole priority. We take great pride in providing you with state-of-the-art eyecare matched with personal attention from our staff and doctors. Your quality of life is our goal and we believe that healthy eyesight is vital to achieving it.</p>
    <p>Our professional and personable staff is highly trained in helping you achieve and maintain healthy eyesight. Our optometrists have combined experiences and specialize in Orthokeratology (OrthoK), Ocular disease, Glaucoma diagnosis &amp; management.</p>
  </div>
</section>

<section class="services">
  <div class="ghost" style="top:490px">WHAT WE DO</div>
  <div class="service-card" style="left:133px;top:27px"><div class="photo" role="img" aria-label="Photo of a family trying on glasses" style="background:linear-gradient(135deg,#e9d4c4,#c89a86)"></div><div class="cap">COMPREHENSIVE EYE EXAMINATIONS</div></div>
  <div class="service-card" style="left:450px;top:27px"><div class="photo" role="img" aria-label="Photo of a contact lens on a fingertip" style="background:linear-gradient(135deg,#cfe3ee,#6fa6c4)"></div><div class="cap">CONTACT LENSES</div></div>
  <div class="service-card" style="left:767px;top:27px"><div class="photo" role="img" aria-label="Close-up photo of an eye" style="background:linear-gradient(135deg,#e8d6c8,#a88571)"></div><div class="cap">EYE INFECTIONS, EYE INJURIES...</div></div>
  <div class="service-card" style="left:133px;top:263px"><div class="photo" role="img" aria-label="Photo of a patient at an eye examination device" style="background:linear-gradient(135deg,#3d6f98,#b8c9d6)"></div><div class="cap">CATARACTS, GLAUCOMA</div></div>
  <div class="service-card" style="left:450px;top:263px"><div class="photo" role="img" aria-label="Photo of a retinal camera scan" style="background:radial-gradient(circle at 60% 50%,#7fd0ef,#1f5f8a 50%,#0c2a44)"></div><div class="cap">RETINAL CAMERA</div></div>
  <div class="service-card" style="left:767px;top:263px"><div class="photo" role="img" aria-label="Close-up photo of an eye with lashes" style="background:linear-gradient(135deg,#f0d9c9,#9a6f5a)"></div><div class="cap">DRY EYES</div></div>
  <div class="more-btn">VIEW MORE SERVICES</div>
</section>

<section class="team">
  <h2 class="title">OUR TEAM</h2>
  <div class="arrow" style="left:37px;top:362px"><svg viewBox="0 0 24 24"><path d="M15 4 7 12l8 8" fill="none" stroke="#555" stroke-width="3"/></svg></div>
  <div class="arrow" style="left:1115px;top:362px"><svg viewBox="0 0 24 24"><path d="m9 4 8 8-8 8" fill="none" stroke="#555" stroke-width="3"/></svg></div>
  <div class="team-card" style="left:116px" role="img" aria-label="Portrait photo of a team member"><div style="position:absolute;inset:0;background:linear-gradient(135deg,#8fa79a,#c9b6a2)"></div></div>
  <div class="team-card feature" style="left:450px">
    <div class="photo" role="img" aria-label="Portrait photo of Dr. Nadia Velt" style="background:linear-gradient(#e3e6e8,#c4b4a6)"></div>
    <div class="label"><div class="nm">DR. NADIA VELT, O.D.</div><div class="rl">Optometrist</div>
      <span class="go"><svg width="14" height="14" viewBox="0 0 24 24"><path d="m9 4 8 8-8 8" fill="none" stroke="#f6c623" stroke-width="3"/></svg></span></div>
  </div>
  <div class="team-card" style="left:784px" role="img" aria-label="Portrait photo of a team member"><div style="position:absolute;inset:0;background:linear-gradient(135deg,#9fb7a8,#d2c0b0)"></div></div>
</section>

<section class="dry">
  <div class="dry-photo" role="img" aria-label="Photo of a person wearing black-framed glasses"></div>
  <div class="dry-frame"></div>
  <div class="play"><svg width="38" height="38" viewBox="0 0 24 24"><path d="M7 4v16l13-8z" fill="#fff"/></svg></div>
  <h2>DRY EYE CLINIC</h2>
  <p>CONTENT TEARS are continuously formed to lubricate the eye and contain natural antibiotics to help fight infections. When constant tears flow is reduced, there is irritation that can cause excessive reflex tearing / watery eyes. These excess tears lack the oil needed to keep from evaporating and do not lubricate the eye.</p>
  <div class="pill">READ MORE</div>
</section>

<section class="reviews">
  <h2 class="title">PATIENT REVIEWS</h2>
  <div class="arrow" style="left:37px;top:320px"><svg viewBox="0 0 24 24"><path d="M15 4 7 12l8 8" fill="none" stroke="#555" stroke-width="3"/></svg></div>
  <div class="arrow" style="left:1115px;top:320px"><svg viewBox="0 0 24 24"><path d="m9 4 8 8-8 8" fill="none" stroke="#555" stroke-width="3"/></svg></div>
  <div class="review" style="left:113px"><div class="q">“</div><p>Lorem ipsum dolor sit amet, consectetur adipiscing elit, sed do eiusmod tempor incididunt</p><div class="src"><i></i>Searchly</div></div>
  <div class="review" style="left:450px"><div class="q">“</div><p>Lorem ipsum dolor sit amet, consectetur adipiscing elit, sed do eiusmod tempor incididunt</p><div class="src"><i></i>Reviewo</div></div>
  <div class="review" style="left:787px"><div class="q">“</div><p>Lorem ipsum dolor sit amet, consectetur adipiscing elit, sed do eiusmod tempor incididunt</p><div class="src"><i></i>Docbook</div></div>
</section>

<section class="partners">
  <div class="partner"></div><div class="partner"></div><div class="partner"></div><div class="partner"></div><div class="partner round"></div><div class="partner"></div>
</section>

<section class="contact">
  <h2 class="title">CONTACT</h2>
  <svg class="band" viewBox="0 0 1200 310" preserveAspectRatio="none"><path d="M0 70 Q600 -40 1200 70 L1200 240 Q600 340 0 240 Z" fill="#167a97"/></svg>
  <div class="ghost" style="top:235px;font-size:90px">GET IN TOUCH</div>
  <div class="map" role="img" aria-label="Street map showing both office locations"></div>
  <svg class="band" viewBox="0 0 1200 310" preserveAspectRatio="none" style="pointer-events:none"><path d="M0 240 Q600 340 0 240 Z M0 220 L0 240 Q600 340 1200 240 L1200 220 Q600 320 0 220Z" fill="#167a97"/></svg>
  <div class="contact-item" style="left:160px"><div class="ic"><svg width="20" height="20" viewBox="0 0 24 24"><path fill="#fff" d="M12 2a7 7 0 0 0-7 7c0 5 7 13 7 13s7-8 7-13a7 7 0 0 0-7-7zm0 9.5A2.5 2.5 0 1 1 12 6.5a2.5 2.5 0 0 1 0 5z"/></svg></div>4180 Larkmere Ave,<br>Vellmont, CA 90001</div>
  <div class="contact-item" style="left:388px"><div class="ic"><svg width="20" height="20" viewBox="0 0 24 24"><path fill="#fff" d="M6.6 10.8a15 15 0 0 0 6.6 6.6l2.2-2.2c.3-.3.7-.4 1-.2 1.1.4 2.3.6 3.6.6.6 0 1 .4 1 1V20c0 .6-.4 1-1 1A17 17 0 0 1 3 4c0-.6.4-1 1-1h3.5c.6 0 1 .4 1 1 0 1.3.2 2.5.6 3.6.1.3 0 .7-.2 1z"/></svg></div>Phone: 555-014-2010<br>Fax: 555-014-2070</div>
  <div class="contact-item" style="left:632px"><div class="ic"><svg width="20" height="20" viewBox="0 0 24 24"><path fill="#fff" d="M3 5h18v14H3zm2 2v.5l7 5 7-5V7l-7 5z"/></svg></div><br>info@brivaloka.com</div>
  <div class="contact-item" style="left:838px"><div class="ic"><svg width="20" height="20" viewBox="0 0 24 24"><circle cx="12" cy="12" r="9" fill="none" stroke="#fff" stroke-width="2"/><path d="M12 7v5l3 2" stroke="#fff" stroke-width="2" fill="none"/></svg></div>Monday - Thursday: 9 am - 6 pm<br>Friday: 8:30 am - 5 pm<br>Saturday: 8:30 am - 1 pm<br>Closed on Sundays</div>
  <div class="info" style="left:200px;width:275px"><h3>Lumora Optometry</h3><ul><li>4180 Larkmere Ave,</li><li>Vellmont, CA 90001</li><li>Phone: 555-014-2010</li><li>Fax: 555-014-2070</li><li>Email: info@brivaloka.com</li></ul></div>
  <div class="info" style="left:725px;width:272px"><h3>Crestvale</h3><ul><li>2250 Ardenfield Rd,</li><li>Crestvale, CA 90002</li><li>Phone: 555-014-3120</li><li>Email: crest@brivaloka.com</li></ul></div>
</section>

<footer class="site-footer">
  <div class="social"><span></span><span></span><span></span><span></span><span></span></div>
  <div class="foot-nav">OUR TEAM<span>/</span>EYECARE<span>/</span>MYOPIA CONTROL CLINIC<span>/</span>DRY EYE CLINIC<span>/</span>EYEWEAR<span>/</span>PATIENT CENTER<span>/</span>CONTACT US</div>
  <div class="copy">Copyright ©2019 Companyname. All Rights Reserved | Terms and Conditions</div>
</footer>

</body>
</html>
```